pipewell new business sales flyer

this is a flyer to tell people what pipewell does and what is great about the service we offer.

please see attached doc for brief, and add the contact details below.

17/22-30 Kessington Rd, Brindale East VIC 3061
03 9471 2608
0428 716 304
bookings@pipewell.com.au
www.pipewell.com.au

Target Market(s)

home builder companies

Industry/Entity Type

residential home building construction

Colors
0054AA
0677BA
7BADD7
CADEEF
E8F1F8
0094D4
00A9DD
6FCCEA
C7EBF8
E9F6FB
FFC000
F8CF3A
FAE287
FDF2CF
FEFAEE

Requirements
Must have
• logo/images/

```html
<!DOCTYPE html>
<html lang="en">
<head>
<meta charset="utf-8">
<title>Pipewell – New Business Sales Flyer</title>
<link href="https://fonts.googleapis.com/css2?family=Bebas+Neue&family=Poppins:wght@400;600;700&family=Saira+Semi+Condensed:wght@700&display=swap" rel="stylesheet">
<style>
  :root{
    --backdrop:#5a5a5a;
    --navy:#22408c;
    --cyan:#00a9dd;
    --sky:#d5f1f8;
    --ink:#222;
    --grey:#555;
    --white:#fff;
  }
  *{margin:0;padding:0;box-sizing:border-box}
  html,body{width:1200px;height:851px;overflow:hidden;background:var(--backdrop)}
  .canvas{position:relative;width:1200px;height:851px}
  .page{position:absolute;top:73px;width:486px;height:688px;overflow:hidden}
  .page--front{left:98px;background:var(--white)}
  .page--back{left:616px;background:var(--sky)}

  .hero-photo{position:absolute;left:0;top:0;width:486px;height:380px;
    background:linear-gradient(180deg,#9a4f42 0%,#8c4a3f 55%,#b8958d 80%,#fff 100%)}
  .front-panel{position:absolute;left:24px;top:275px;width:433px;height:413px;background:var(--sky)}

  .brand{position:absolute;left:0;width:100%;display:flex;justify-content:center;align-items:center;gap:6px;
    font-family:"Poppins",sans-serif;font-weight:700;color:var(--navy);letter-spacing:-2px;line-height:1}
  .brand__dot{width:14px;height:14px;border-radius:50%;background:var(--cyan);align-self:flex-end;margin-bottom:6px}
  .page--front .brand{top:40px;font-size:52px}
  .page--back .brand{top:28px;font-size:58px}

  .headline{font-family:"Bebas Neue",sans-serif;font-weight:400;color:var(--navy)}
  .headline .accent{color:var(--cyan)}
  .front-panel .headline{position:absolute;top:110px;width:100%;text-align:center;font-size:22px;letter-spacing:.2px}
  .front-copy{position:absolute;left:48px;top:146px;width:345px;font-family:"Poppins",sans-serif;font-size:11.6px;line-height:14.6px;color:var(--ink);text-align:justify;text-align-last:center}
  .front-copy p+p{margin-top:14px}

  .contact-band{position:absolute;left:0;width:486px;background:var(--navy);display:flex;justify-content:center;align-items:center}
  .contact-band__text{font-family:"Saira Semi Condensed",sans-serif;font-weight:700;font-size:24px;letter-spacing:.5px}
  .page--front .contact-band{top:629px;height:40px}
  .page--front .contact-band__inner{width:430px;height:40px;background:var(--cyan);display:flex;align-items:center;justify-content:center}
  .page--front .contact-band__text{color:var(--white)}
  .page--back .contact-band{top:625px;height:37px}
  .page--back .contact-band__text{color:var(--cyan)}

  .service-title{position:absolute;top:107px;width:100%;text-align:center;font-family:"Poppins",sans-serif;font-weight:700;font-size:19.5px;color:var(--navy)}
  .service-title .accent{color:var(--cyan)}
  .gallery{position:absolute;top:163px;left:25px;display:flex;gap:4px}
  .gallery__item{width:142px;height:140px;border:1px solid #888}
  .gallery__item--pipe{background:radial-gradient(circle at 40% 35%,#2a2516 0%,#6e6440 35%,#c9c28f 75%,#e8e3b8 100%)}
  .gallery__item--wall{background:linear-gradient(135deg,#f4f4f4,#dcdcdc)}
  .gallery__item--camera{background:radial-gradient(circle at 55% 40%,#5b6a3a 0%,#8f9a6a 50%,#c9cdae 100%);border-color:#6a7a5a}

  .page--back .headline{position:absolute;left:33px;top:328px;font-size:31px;word-spacing:6px}
  .back-copy{position:absolute;left:33px;top:374px;width:427px;font-family:"Poppins",sans-serif;font-size:10.6px;line-height:12.6px;color:var(--grey);text-align:justify}
  .back-copy p+p{margin-top:12px}
  .benefits{position:absolute;left:31px;top:511px;width:380px;list-style:none;font-family:"Poppins",sans-serif;font-weight:600;font-size:10.6px;line-height:12.6px;color:#333}
  .benefits li{display:flex;gap:11px;margin-bottom:12px}
  .benefits li:nth-child(2){margin-bottom:18px}
  .benefits svg{flex:none;margin-top:0}
  .benefits span{text-align:justify}
</style>
</head>
<body>
<div class="canvas">

  <section class="page page--front">
    <div class="hero-photo" role="img" aria-label="Photo of a red brick wall with a stepped crack running through the mortar"></div>
    <div class="front-panel">
      <div class="brand"><span class="brand__name">pipewell</span><span class="brand__dot"></span></div>
      <h2 class="headline">What is slab heave <span class="accent">costing your business?</span></h2>
      <div class="front-copy">
        <p>The RBC (Regional Building Council) put out a report regarding the growing concern of slab heave in new homes.</p>
        <p>One of their recommendations to eliminate the problem is to conduct an independent inspection (rather than self-certification) of installed stormwater drainage systems. This should be an extension of mandatory inspections for building structures.</p>
        <p>Pipewell are the only specialized drainage inspectors to offer a cost-effective independent solution to inspect drains on each site. We are saving our home builder clients a lot of money. Talk to us today about how.</p>
      </div>
    </div>
    <div class="contact-band"><div class="contact-band__inner"><span class="contact-band__text">369-481-2270 | PIPEWELL.COM</span></div></div>
  </section>

  <section class="page page--back">
    <div class="brand"><span class="brand__name">pipewell</span><span class="brand__dot"></span></div>
    <h1 class="service-title">CCTV Drain <span class="accent">Inspection+ Repairs</span></h1>
    <div class="gallery">
      <div class="gallery__item gallery__item--pipe" role="img" aria-label="Camera view inside a drain pipe with debris"></div>
      <div class="gallery__item gallery__item--wall" role="img" aria-label="Crack running down a white plastered wall"></div>
      <div class="gallery__item gallery__item--camera" role="img" aria-label="CCTV camera footage of a damaged pipe"></div>
    </div>
    <h2 class="headline">Pipewell What we do?</h2>
    <div class="back-copy">
      <p>Long-term sewer &amp; stormwater damage on new home builds is hitting builders where it hurts, it severely impacts both your reputation and your bank balance. We've got the solution!</p>
      <p>Our fixed-price Drainage Inspection Package catches issues before homeowners move in. Our Post-Slab &amp;Pre Settlement Drain Inspection on every build, sees repairs fixed on the spot, all included in the one low fixed-price. You'll receive a comprehensive report &amp; video footage for each inspection. We pride ourselves on our reputation, customer service is at the forefront of everything we do.</p>
    </div>
    <ul class="benefits">
      <li><svg width="12" height="12" viewBox="0 0 12 12" aria-hidden="true"><circle cx="6" cy="6" r="5" fill="none" stroke="#22408c" stroke-width="1.6"/><path d="M3.4 6l2 2L10.5 2.5" fill="none" stroke="#22408c" stroke-width="1.8"/></svg><span>We have the capacity to take on the largest volume builders!</span></li>
      <li><svg width="12" height="12" viewBox="0 0 12 12" aria-hidden="true"><circle cx="6" cy="6" r="5" fill="none" stroke="#22408c" stroke-width="1.6"/><path d="M3.4 6l2 2L10.5 2.5" fill="none" stroke="#22408c" stroke-width="1.8"/></svg><span>With over 50,000 jobs under our belt, we know a thing or two about drainage problems.</span></li>
      <li><svg width="12" height="12" viewBox="0 0 12 12" aria-hidden="true"><circle cx="6" cy="6" r="5" fill="none" stroke="#22408c" stroke-width="1.6"/><path d="M3.4 6l2 2L10.5 2.5" fill="none" stroke="#22408c" stroke-width="1.8"/></svg><span>Did you know? From the homes we've inspected every second home built has on average 2 breaks in the storm water.</span></li>
    </ul>
    <div class="contact-band"><span class="contact-band__text">369-481-2270 | PIPEWELL.COM</span></div>
  </section>

</div>
</body>
</html>
```